Commercial Swimming Pool - Design-Build Contractor Website Design

I need a new website that will feature our newly developed logo and trade name as well as provide a fully updated site experience. We are not a residential builder - we strictly design and install high-end commercial pools. I need the website to highlight our portfolio and communicate the various types of projects in which we specialize. I want the effect of the site to reflect the high-end nature of our services - projects like the 57th floor spa at the Phila Silver Willow, the aquatic therapy portion of the Phila Ravenhawks training facility, a 5om indoor competition pool for the prestigious Dallowmere Academy, the indoor water park at The Quenwick Lodge or the recent country club renovation projects we've completed in our region (to name a few examples).
Need extra days to review

```html
<!DOCTYPE html>
<html lang="en">
<head>
<meta charset="utf-8">
<title>Marlowe Aquatics</title>
<link href="https://fonts.googleapis.com/css2?family=Poppins:wght@400;500;600;700&display=swap" rel="stylesheet">
<style>
:root{
  --navy:#1c2a5e;
  --navy-deep:#16224f;
  --sky:#2fa8dc;
  --sky-light:#5cc3ec;
  --ink:#222;
  --muted:#555;
  --white:#fff;
  --black:#0b0b0b;
  --card-line:#e3e3e3;
}
*{box-sizing:border-box;margin:0;padding:0}
html,body{width:1200px;height:3444px;overflow:hidden;background:var(--white);font-family:"Poppins",sans-serif;color:var(--ink)}
.page{position:relative;width:1200px;height:3444px;overflow:hidden}

/* header */
.site-header{position:absolute;top:0;left:0;width:1200px;height:76px;background:var(--white);z-index:5;display:flex;align-items:center;padding:0 100px}
.brand{display:flex;align-items:center;gap:10px}
.brand-dot{width:26px;height:26px;background:var(--sky);border-radius:50%}
.brand-name{font-size:26px;font-weight:700;color:var(--navy);letter-spacing:.5px}
.main-nav{margin-left:auto;display:flex;align-items:center;gap:30px;font-size:16px;font-weight:500}
.main-nav a{color:var(--ink);text-decoration:none}
.main-nav a.active{color:var(--sky);border-bottom:2px solid var(--sky)}
.btn{display:inline-block;background:var(--sky);color:var(--white);font-weight:600;border-radius:30px;text-decoration:none}
.main-nav .btn{padding:10px 20px;font-size:16px;color:var(--white)}

/* hero */
.hero{position:absolute;top:76px;left:0;width:1200px;height:720px}
.hero-photo{position:absolute;inset:0;background:linear-gradient(180deg,#7a8fa8 0%,#5b6e82 30%,#8a7a66 62%,#6a5440 100%)}
.hero-wave{position:absolute;left:0;bottom:0;width:1200px;height:200px}
.hero-content{position:absolute;top:180px;left:0;width:1200px;text-align:center;color:var(--white)}
.hero-title{font-size:46px;font-weight:700;letter-spacing:1px;text-shadow:0 2px 6px rgba(0,0,0,.4)}
.hero-text{width:760px;margin:10px auto 0;font-size:14px;line-height:1.6}
.hero .btn{margin-top:28px;padding:12px 26px;font-size:16px}
.arrow{position:absolute;width:30px;height:30px;border-radius:50%;background:var(--white);display:flex;align-items:center;justify-content:center}

/* projects */
.section-title{position:absolute;width:1200px;text-align:center;font-size:34px;font-weight:700;color:var(--navy)}
.section-title span{color:var(--sky)}
.project-card{position:absolute;top:860px;width:320px;height:330px;background:var(--white);border:1px solid var(--card-line);box-shadow:0 4px 14px rgba(0,0,0,.1);text-align:center;padding:30px 26px}
.project-icon{width:96px;height:96px;margin:0 auto;border-radius:50%;background:var(--navy);border:5px solid #cfe9f6}
.project-card h3{margin-top:22px;font-size:17px;font-weight:600;line-height:1.45;color:var(--ink)}
.project-card p{margin-top:14px;font-size:14px;line-height:1.6;color:var(--muted)}

/* about band */
.about-band{position:absolute;top:1360px;left:0;width:1200px;height:880px}
.service-circle{position:absolute;top:1270px;width:340px;height:340px;border-radius:50%;border:6px solid var(--white);display:flex;align-items:center;justify-content:center;color:var(--white);font-size:19px;font-weight:600;text-shadow:0 2px 4px rgba(0,0,0,.5);z-index:3}
.about-mark{position:absolute;top:1740px;left:100px;width:440px;font-size:58px;font-weight:700;color:var(--white);line-height:1.1}
.about-copy{position:absolute;top:1660px;left:585px;width:520px;color:var(--white)}
.about-copy h2{font-size:34px;font-weight:700}
.about-copy p{margin-top:14px;font-size:14px;line-height:1.75;color:#d9def0}
.about-copy .btn{margin-top:22px;padding:12px 26px;font-size:16px}

/* portfolio */
.portfolio-tile{position:absolute}
.portfolio-label{position:absolute;inset:0;display:flex;flex-direction:column;align-items:center;justify-content:center;color:var(--white);font-size:17px;font-weight:500;background:rgba(0,0,0,.25)}

/* footer */
.site-footer{position:absolute;top:3116px;left:0;width:1200px;height:328px;background:var(--black);color:var(--white)}
.footer-brand{position:absolute;top:44px;left:100px}
.footer-brand .brand-name{color:var(--white)}
.socials{display:flex;gap:10px;margin-top:24px}
.socials i{width:26px;height:26px;border-radius:50%;background:var(--white);display:block}
.footer-col{position:absolute;top:44px}
.footer-col h4{font-size:20px;font-weight:600;margin-bottom:18px}
.footer-col li{list-style:none;font-size:14px;margin-bottom:10px;display:flex;align-items:center;gap:10px}
.bullet{width:6px;height:6px;background:var(--white);border-radius:50%}
.newsletter-input{width:210px;height:42px;border-radius:22px;background:var(--white);color:#888;font-size:12px;padding:0 18px;display:flex;align-items:center}
.newsletter .btn{margin-top:14px;width:210px;height:42px;line-height:42px;text-align:center;font-size:16px}
.copyright{position:absolute;bottom:0;left:0;width:1200px;height:52px;border-top:1px solid #333;text-align:center;line-height:52px;font-size:13px}
</style>
</head>
<body>
<div class="page">

<header class="site-header">
  <div class="brand"><i class="brand-dot"></i><span class="brand-name">Marlowe Aquatics</span></div>
  <nav class="main-nav">
    <a class="active" href="#">Home</a>
    <a href="#">About Us</a>
    <a href="#">Projects</a>
    <a href="#">Our Portfolio</a>
    <a class="btn" href="#">Contact Us</a>
  </nav>
</header>

<section class="hero">
  <div class="hero-photo" role="img" aria-label="Rooftop pool with wooden deck beside a modern building"></div>
  <svg class="hero-wave" viewBox="0 0 1200 200" preserveAspectRatio="none">
    <path d="M0 110 Q300 190 620 130 T1200 10 L1200 200 L0 200Z" fill="var(--sky)"/>
    <path d="M0 150 Q320 215 640 150 T1200 45 L1200 200 L0 200Z" fill="var(--white)"/>
  </svg>
  <div class="arrow" style="left:20px;top:340px"><svg width="12" height="12" viewBox="0 0 12 12"><path d="M8 1 3 6l5 5" stroke="#222" stroke-width="2" fill="none"/></svg></div>
  <div class="arrow" style="right:20px;top:340px"><svg width="12" height="12" viewBox="0 0 12 12"><path d="M4 1l5 5-5 5" stroke="#222" stroke-width="2" fill="none"/></svg></div>
  <div class="hero-content">
    <h1 class="hero-title">WELCOME TO MARLOWE AQUATICS</h1>
    <p class="hero-text">Lorem ipsum dolor sit amet, consectetur adipiscing elit, sed do eiusmod tempor incididunt ut labore et dolore magna aliqua. Ut enim ad minim veniam, quis nostrud exercitation ullamco laboris nisi ut ea commodo consequat.</p>
    <a class="btn" href="#">Get Started</a>
  </div>
</section>

<h2 class="section-title" style="top:776px"><span>Our</span> Projects</h2>
<div class="arrow" style="left:30px;top:980px;box-shadow:0 0 4px rgba(0,0,0,.2)"><svg width="10" height="10" viewBox="0 0 12 12"><path d="M8 1 3 6l5 5" stroke="#222" stroke-width="2" fill="none"/></svg></div>
<div class="arrow" style="left:1140px;top:980px;box-shadow:0 0 4px rgba(0,0,0,.2)"><svg width="10" height="10" viewBox="0 0 12 12"><path d="M4 1l5 5-5 5" stroke="#222" stroke-width="2" fill="none"/></svg></div>

<article class="project-card" style="left:100px">
  <div class="project-icon"></div>
  <h3>57th floor spa at the Phila Silver Willow</h3>
  <p>Lorem ipsum dolor sit amet, eiusmod tempor incididunt magna aliqua.</p>
</article>
<article class="project-card" style="left:440px">
  <div class="project-icon"></div>
  <h3>The Aquatic Therapy Portion of the Phila Ravenhawks Training Facility</h3>
  <p>Lorem ipsum dolor sit amet, eiusmod tempor incididunt magna aliqua.</p>
</article>
<article class="project-card" style="left:780px">
  <div class="project-icon"></div>
  <h3>A 5om Indoor Competition Pool for the Prestigious Dallowmere Academy</h3>
  <p>Lorem ipsum dolor sit amet, eiusmod tempor incididunt magna aliqua.</p>
</article>

<section class="about-band">
  <svg width="1200" height="880" viewBox="0 0 1200 880" style="position:absolute;inset:0">
    <path d="M0 40 Q600 -40 1200 40 L1200 780 Q700 900 0 800Z" fill="var(--sky)"/>
    <path d="M0 70 Q600 0 1200 60 L1200 760 Q700 870 0 780Z" fill="var(--navy)"/>
  </svg>
</section>

<div class="service-circle" style="left:110px;background:linear-gradient(160deg,#5c7d8e,#2e4b5c)" role="img" aria-label="Commercial pool photo">Commercial Pools</div>
<div class="service-circle" style="left:430px;background:linear-gradient(160deg,#6aa8c4,#2d6d8a)" role="img" aria-label="Pool water with chlorine wash">Chlorine Washes</div>
<div class="service-circle" style="left:750px;background:linear-gradient(160deg,#4a9fcf,#1f5d86)" role="img" aria-label="Automatic pool cleaner underwater">Automatic Chemical Pool</div>

<div class="about-mark">Marlowe<br>Aquatics</div>
<div class="about-copy">
  <h2>About Us</h2>
  <p>Sed ut perspiciatis unde omnis iste natus error sit voluptatem accusantium doloremque laudantium, totam rem aperiam, eaque ipsa quae ab illo inventore veritatis et quasi architecto beatae vitae dicta sunt explicabo. Nemo enim ipsam voluptatem quia voluptas sit aspernatur aut odit aut fugit, sed quia consequuntur magni dolores eos qui ratione voluptatem sequi nesciunt. Neque porro quisquam est, qui dolorem ipsum quia dolor sit amet, consectetur, adipisci velit, sed quia non numquam eius modi tempora incidunt ut labore et dolore magnam aliquam quaerat voluptatem. Ut enim ad minima veniam, quis nostrum exercitationem ullam corporis suscipit laboriosam, nisi ut aliquid ex ea commodi consequatur?</p>
  <a class="btn" href="#">Read More</a>
</div>

<h2 class="section-title" style="top:2208px"><span>Our</span> Portfolio</h2>

<div class="portfolio-tile" style="left:100px;top:2280px;width:472px;height:356px;background:linear-gradient(160deg,#6f8a5a,#4aa3cf 60%,#b9a98c)" role="img" aria-label="Backyard-style pool with stone deck"></div>
<div class="portfolio-tile" style="left:588px;top:2280px;width:244px;height:356px;background:linear-gradient(180deg,#9ec0c8,#3aa6b4 55%,#2f7f86)" role="img" aria-label="Infinity pool facing the sea"></div>
<div class="portfolio-tile" style="left:848px;top:2280px;width:252px;height:356px;background:linear-gradient(180deg,#6fb4e6,#8fb06a 50%,#35a7d8)" role="img" aria-label="Resort pool lined with palm trees"></div>
<div class="portfolio-tile" style="left:100px;top:2648px;width:248px;height:404px;background:linear-gradient(180deg,#d8b48a,#c89a70 50%,#3aa0c8)" role="img" aria-label="Guests relaxing in a spa pool"></div>
<div class="portfolio-tile" style="left:364px;top:2648px;width:468px;height:404px;background:linear-gradient(160deg,#2f3a46,#1d4a5a 60%,#123040)" role="img" aria-label="Commercial pool at dusk">
  <div class="portfolio-label">Commercial Pools
    <svg width="26" height="26" viewBox="0 0 24 24" style="margin-top:14px"><circle cx="10" cy="10" r="7" stroke="#fff" stroke-width="2.5" fill="none"/><path d="M15 15l6 6" stroke="#fff" stroke-width="2.5"/></svg>
  </div>
</div>
<div class="portfolio-tile" style="left:848px;top:2648px;width:252px;height:404px;background:linear-gradient(180deg,#7fb7e0,#5a8a5a 45%,#2b9ed4)" role="img" aria-label="Hotel pool with palm trees"></div>

<footer class="site-footer">
  <div class="footer-brand">
    <div class="brand"><i class="brand-dot"></i><span class="brand-name">Marlowe Aquatics</span></div>
    <div class="socials"><i></i><i></i><i></i><i></i><i></i></div>
  </div>
  <div class="footer-col" style="left:410px">
    <h4>Contact Us</h4>
    <ul>
      <li><svg width="14" height="14" viewBox="0 0 24 24"><path d="M6 2l4 4-2 3c1 3 4 6 7 7l3-2 4 4-3 4C10 22 2 14 2 5z" fill="#fff"/></svg>+1 555 0100 2000</li>
      <li><svg width="14" height="14" viewBox="0 0 24 24"><rect x="2" y="5" width="20" height="14" fill="none" stroke="#fff" stroke-width="2"/><path d="M2 6l10 7 10-7" fill="none" stroke="#fff" stroke-width="2"/></svg>info@harborlineintl.example</li>
      <li><svg width="14" height="14" viewBox="0 0 24 24"><path d="M12 2a7 7 0 0 0-7 7c0 5 7 13 7 13s7-8 7-13a7 7 0 0 0-7-7z" fill="#fff"/><circle cx="12" cy="9" r="2.5" fill="#000"/></svg>Harborline International, United States</li>
    </ul>
  </div>
  <div class="footer-col" style="left:720px">
    <h4>Quick Links</h4>
    <ul>
      <li><i class="bullet"></i>Home</li>
      <li><i class="bullet"></i>About Us</li>
      <li><i class="bullet"></i>Services</li>
      <li><i class="bullet"></i>Testimonials</li>
      <li><i class="bullet"></i>Blog</li>
    </ul>
  </div>
  <div class="footer-col newsletter" style="left:888px">
    <h4>Join Our Newsletter</h4>
    <div class="newsletter-input">Enter Email Address</div>
    <a class="btn" href="#">Subscribe</a>
  </div>
  <div class="copyright">Copyright©2023 Marlowe Aquatics All Rights Reserved</div>
</footer>

</div>
</body>
</html>
```